Tavenhurst Falcons FC Website

We are looking to develop a new website for Tavenhurst FC. Tavenhurst FC has now joined with Tavenhurst Falcons FC and we are looking at a website that can work for both clubs. Tavenhurst FC play in a local park football competition while tavenhurst Falcons are a Semi Professional team that plays in the Ostral Premier Series Competition. What we are after is two separate website off the one platform. I have attached both team logos for you to visualise. Also you can look at the existing tavenhurst website www.tavenhurstfc.net.au. We are looking for a huge improvement in the website and it will be imperative we have links to sponsors and the sponsors can get regular visuals. Weare looking to move this club forward and have a very professional website that can communicate clearly with the community.

Hi All,

Please remember that the website is to represent two clubs;
1. Tavenhurst Falcons FC (Competes in Semi Professional League)
2. Tavenhurst FC (Compete in KPWLT League which is a lower level)

Further to this the Tavenhurst Falcons FC page will require a player profile page which will show photos of each player and a little bio on each.

Thanks

Reason: Would like to spend more time review existing and new designs

```html
<!DOCTYPE html>
<html lang="en">
<head>
<meta charset="utf-8">
<title>Tavenhurst FC</title>
<link rel="stylesheet" href="https://fonts.googleapis.com/css2?family=Play:wght@400;700&family=Mulish:wght@400;600;700&display=swap">
<style>
:root{
  --red:#d4171f;
  --red-dark:#a80f16;
  --ink:#2b2b2b;
  --text:#6a6a6a;
  --light:#efefef;
  --white:#ffffff;
  --footer:#1d1d1d;
  --footer-text:#a9a9a9;
  --rule:#3a3a3a;
}
*{box-sizing:border-box;margin:0;padding:0}
html,body{width:685px;height:1200px;overflow:hidden;background:var(--white)}
body{position:relative;font-family:"Mulish",Arial,sans-serif;color:var(--text)}
.abs{position:absolute}
.heading{font-family:"Play",Arial,sans-serif;font-weight:400;text-transform:uppercase;letter-spacing:.5px;white-space:nowrap}
.accent{color:var(--red)}

/* top bar + nav */
.top-strip{left:0;top:0;width:685px;height:20px;background:linear-gradient(#2a2a2a,#4a4a4a)}
.nav{left:0;top:20px;width:685px;height:32px;background:var(--white);border-bottom:1px solid #ddd}
.nav a{position:absolute;top:11px;font-family:"Play",Arial,sans-serif;font-size:7.5px;color:var(--ink);text-decoration:none;text-transform:uppercase}
.nav a.active{color:var(--red)}
.nav .active-bar{position:absolute;left:92px;top:30px;width:40px;height:2px;background:var(--red)}
.nav-brand{left:308px;top:0;width:70px;height:64px;background:var(--white);border-radius:0 0 34px 34px;display:flex;flex-direction:column;align-items:center;justify-content:center;gap:4px;box-shadow:0 2px 4px rgba(0,0,0,.15)}
.nav-brand .dot{width:18px;height:18px;border-radius:50%;background:var(--red)}
.nav-brand span{font-family:"Play",Arial,sans-serif;font-size:6.5px;font-weight:400;color:var(--red);text-align:center;line-height:1.1}

/* hero */
.hero{left:0;top:52px;width:685px;height:266px;background:radial-gradient(ellipse at 60% 30%,#cdb48a 0%,#8a6f4a 35%,#3d3226 75%,#1c1712 100%)}
.hero-arrow{width:24px;height:24px;border-radius:50%;border:1.5px solid var(--white);display:flex;align-items:center;justify-content:center}
.hero-arrow.next{border-color:var(--red)}
.hero-brand{left:92px;top:190px;width:64px;height:64px;border-radius:50%;background:var(--red);border:3px solid var(--white)}
.hero-title{left:167px;top:186px;font-size:26px;color:var(--red)}
.hero-text{left:167px;top:217px;width:200px;font-size:7.5px;line-height:1.6;color:var(--white)}

/* welcome */
.welcome{left:0;top:318px;width:685px;height:156px;background:linear-gradient(90deg,#e6e6e6,#f2f2f2 50%,#e6e6e6)}
.welcome-title{left:92px;top:343px;font-size:20px;line-height:1.2;color:var(--ink);letter-spacing:.3px}
.register{left:92px;top:402px;width:163px;height:49px;background:linear-gradient(var(--red),var(--red-dark));color:var(--white);padding:10px 0 0 44px}
.register .season{font-family:"Play",Arial,sans-serif;font-size:9px;font-variant:small-caps;letter-spacing:.5px}
.register .cta{font-family:"Play",Arial,sans-serif;font-size:12.5px;text-transform:uppercase;letter-spacing:.5px}
.talk-title{left:280px;top:345px;font-size:14px;color:var(--ink)}
.talk-rule{left:280px;top:368px;width:313px;height:1px;background:var(--ink)}
.talk-text{left:281px;top:378px;width:312px;font-size:7.4px;line-height:1.6}

/* fixtures */
.fixtures-title{left:91px;top:504px;font-size:18.5px;color:var(--red)}
.fixtures-title .amp{color:var(--ink)}
.fixtures-rule{left:91px;top:535px;width:358px;height:1px;background:var(--ink)}
.fixtures-text{left:92px;top:547px;width:352px;font-size:7.4px;line-height:1.6}
.fixture-list{list-style:none;width:140px}
.fixture-list li{position:relative;padding-left:12px;height:14.65px;font-family:"Play",Arial,sans-serif;font-size:8px;color:var(--ink);text-transform:uppercase}
.fixture-list li::before{content:"";position:absolute;left:0;top:2px;width:4px;height:4px;border:1px solid var(--ink)}
.fixture-list li.current{color:var(--red)}
.fixture-list li.current::before{border-color:var(--red)}
.player{left:474px;top:492px;width:122px;height:280px;background:linear-gradient(180deg,#e9d9d4 0%,#b0262c 30%,#8c1419 70%,#f2eaea 100%);border-radius:30px 30px 6px 6px;opacity:.9}

/* no smoking */
.notice{left:0;top:774px;width:685px;height:120px;background:radial-gradient(ellipse at 50% 50%,#8a8a8a 0%,#5e5e5e 55%,#3a3a3a 100%)}
.notice-title{left:295px;top:796px;font-size:17px;color:var(--white)}
.notice-rule{left:296px;top:826px;width:187px;height:1px;background:#cfcfcf}
.notice-text{left:297px;top:833px;font-size:7.5px;color:var(--white)}
.notice-btn{left:298px;top:851px;width:64px;height:19px;background:var(--red);color:var(--white);font-family:"Play",Arial,sans-serif;font-size:7.5px;font-variant:small-caps;display:flex;align-items:center;justify-content:center}

/* sponsors */
.sponsors{left:0;top:894px;width:685px;height:106px;background:#f4f4f4}
.sponsors-title{left:0;top:916px;width:685px;text-align:center;font-size:15px;color:var(--ink)}
.sponsors-rule{left:92px;top:941px;width:500px;height:1px;background:#d6d6d6}
.sponsor{top:956px;width:72px;height:28px;display:flex;align-items:center;justify-content:center;gap:3px;font-size:7px;font-weight:700;color:var(--ink);text-align:center;line-height:1.1}
.sponsor .mark{flex:none;width:9px;height:9px;background:var(--red)}
.sponsor-divider{top:958px;width:1px;height:26px;background:#dcdcdc}

/* footer */
.footer{left:0;top:1000px;width:685px;height:200px;background:var(--footer)}
.footer-heading{top:1030px;font-size:11px;color:var(--footer-text)}
.footer-heading-rule{left:92px;top:1051px;width:91px;height:1px;background:var(--rule)}
.sitemap{list-style:none;left:92px;top:1059px}
.sitemap li{position:relative;padding-left:11px;height:14.65px;font-size:7px;color:var(--footer-text)}
.sitemap li::before{content:"";position:absolute;left:0;top:2px;width:3.5px;height:3.5px;border:1px solid var(--footer-text)}
.news-item{left:242px;width:150px;height:26px}
.news-thumb{position:absolute;left:0;top:0;width:34px;height:24px;background:linear-gradient(135deg,#8d8d8d,#3f3f3f)}
.news-text{position:absolute;left:39px;top:0;font-size:6px;font-weight:600;color:#d8d8d8;line-height:1.25}
.news-date{position:absolute;left:39px;top:16px;font-size:4.8px;font-style:italic;color:#8a8a8a}
.view-all{left:570px;top:1034px;font-size:6px;color:var(--red-dark)}
.gallery{left:445px;top:1061px;width:147px;height:94px;display:grid;grid-template-columns:repeat(3,1fr);grid-template-rows:repeat(3,1fr);gap:1px}
.gallery div{background:linear-gradient(135deg,#9a6a62,#4e4a4a)}
.gallery .red{background:linear-gradient(135deg,#c2343a,#5a2a2a)}
.gallery .green{background:linear-gradient(135deg,#6a7a52,#3a3a34)}
.footer-rule{left:92px;top:1170px;width:500px;height:1px;background:var(--rule)}
.copyright{left:92px;top:1180px;font-size:6.8px;color:#8a8a8a}
.social{top:1176px;width:14px;height:14px;border-radius:50%;border:1px solid #7a7a7a}
.social.first{border-color:#3b8fd6}
</style>
</head>
<body>

<div class="abs top-strip"></div>

<nav class="abs nav">
  <a class="active" style="left:101px">Home</a>
  <a style="left:138px">About Us</a>
  <a style="left:187px">News</a>
  <a style="left:223px">Fixture &amp; Results</a>
  <a style="left:391px">Photo Gallery</a>
  <a style="left:461px">Sponsor</a>
  <a style="left:509px">Club</a>
  <a style="left:541px">Contact Us</a>
  <div class="active-bar"></div>
</nav>
<div class="abs nav-brand"><div class="dot"></div><span>TAVENHURST<br>FC</span></div>

<section class="abs hero" role="img" aria-label="Action photo of a young footballer kicking a ball toward a goalkeeper in a stadium at dusk"></section>
<div class="abs hero-arrow prev" style="left:38px;top:162px">
  <svg width="8" height="8" viewBox="0 0 8 8"><path d="M5 1 2 4l3 3" fill="none" stroke="#fff" stroke-width="1.4"/></svg>
</div>
<div class="abs hero-arrow next" style="left:622px;top:162px">
  <svg width="8" height="8" viewBox="0 0 8 8"><path d="M3 1l3 3-3 3" fill="none" stroke="#d4171f" stroke-width="1.4"/></svg>
</div>
<div class="abs hero-brand"></div>
<h1 class="abs heading hero-title">Tavenhurst FC</h1>
<p class="abs hero-text">Lorem Ipsum is simply dummy text of the printing and typesetting industry. Lorem Ipsum has been the industry's standard dummy text .</p>

<section class="abs welcome" role="img" aria-label="Faint collage of club member portraits"></section>
<h2 class="abs heading welcome-title">Welcome to<br><span class="accent">Tavenhurst FC</span></h2>
<a class="abs register"><div class="season">2014 Season</div><div class="cta">Register Online</div></a>
<h2 class="abs heading talk-title">Let’s talk <span class="accent">about</span> Tavenhurst FC.</h2>
<div class="abs talk-rule"></div>
<p class="abs talk-text">Lorem Ipsum is simply dummy text of the printing and typesetting industry. Lorem Ipsum has been the industry's standard dummy text ever since the 1500s, when an unknown printer took a galley of type and scrambled it to make a type specimen book. It has survived not only five centuries, but also the leap into electronic typesetting, remaining essentially unchanged. It was popularised in the 1960s with the release of Letraset sheets containing Lorem Ipsum passages.</p>

<h2 class="abs heading fixtures-title">Fixtures <span class="amp">&amp;</span> Results</h2>
<div class="abs fixtures-rule"></div>
<p class="abs fixtures-text">Lorem Ipsum is simply dummy text of the printing and typesetting industry. Lorem Ipsum has been the industry's standard dummy text ever since the 1500s, when an unknown printer took a galley of type and scrambled it to make a type specimen book.</p>

<ul class="abs fixture-list" style="left:92px;top:602px">
  <li>Premier League</li><li class="current">Premier League Res</li><li>Super League</li><li>Super League Res</li><li>Under 16 / 2</li><li>Under 17 / 1</li><li>Under 10 / 2</li><li>Under 10 / 3</li><li>Under 11 / 1</li><li>Under 12 / 3</li>
</ul>
<ul class="abs fixture-list" style="left:242px;top:602px">
  <li>Under 13 / 3</li><li>Under 14 / 3</li><li>AA Men / 5</li><li>AA Men / 6</li><li>AA Men / 8</li><li>AA Men / 10</li><li>AA Men / 10</li><li>AA Men / 14</li><li>07 ECL / Red</li><li>07 ECL / Green</li>
</ul>
<ul class="abs fixture-list" style="left:367px;top:602px">
  <li>07 ECL / Blue</li><li>08 ECL / Blue</li><li>08 ECL / Green</li><li>09 / Green</li><li>06 / A Green</li><li>06 / B Blue</li><li>06 / C Red</li><li>06 / D Purple</li><li>06 / E White</li><li>06 / F Brown</li>
</ul>
<div class="abs player" role="img" aria-label="Cut-out of a footballer in a red kit standing with arms folded beside a ball"></div>

<section class="abs notice" role="img" aria-label="Blurred close-up of a cigarette with smoke"></section>
<svg class="abs" style="left:201px;top:798px" width="72" height="72" viewBox="0 0 72 72" aria-hidden="true">
  <circle cx="36" cy="36" r="36" fill="#fff"/>
  <circle cx="36" cy="36" r="26" fill="none" stroke="#5a5a5a" stroke-width="5"/>
  <rect x="17" y="36" width="30" height="7" fill="#5a5a5a"/>
  <rect x="49" y="36" width="3" height="7" fill="#5a5a5a"/>
  <rect x="54" y="36" width="3" height="7" fill="#5a5a5a"/>
  <path d="M50 33c0-5 5-4 5-9" fill="none" stroke="#5a5a5a" stroke-width="2"/>
  <line x1="18" y1="18" x2="54" y2="54" stroke="#5a5a5a" stroke-width="5"/>
</svg>
<h2 class="abs heading notice-title">No Smoking</h2>
<div class="abs notice-rule"></div>
<p class="abs notice-text">There is a No Smoking Ban for all Sports Grounds</p>
<a class="abs notice-btn">Learn More</a>

<section class="abs sponsors"></section>
<h2 class="abs heading sponsors-title">Our <span class="accent">Sponsors</span></h2>
<div class="abs sponsors-rule"></div>
<svg class="abs" style="left:84px;top:962px" width="10" height="16" viewBox="0 0 10 16" aria-hidden="true"><path d="M8 1 2 8l6 7" fill="none" stroke="#aaa" stroke-width="1.5"/></svg>
<svg class="abs" style="left:592px;top:962px" width="10" height="16" viewBox="0 0 10 16" aria-hidden="true"><path d="M2 1l6 7-6 7" fill="none" stroke="#d4171f" stroke-width="1.8"/></svg>
<div class="abs sponsor" style="left:108px"><span class="mark"></span>Brightside Media</div>
<div class="abs sponsor-divider" style="left:187px"></div>
<div class="abs sponsor" style="left:195px">Kestrel Co</div>
<div class="abs sponsor-divider" style="left:268px"></div>
<div class="abs sponsor" style="left:275px">Novaline</div>
<div class="abs sponsor-divider" style="left:351px"></div>
<div class="abs sponsor" style="left:363px">Harlow &amp; Reed</div>
<div class="abs sponsor-divider" style="left:446px"></div>
<div class="abs sponsor" style="left:452px">Tidewell Seal</div>
<div class="abs sponsor-divider" style="left:527px"></div>
<div class="abs sponsor" style="left:530px;width:54px;font-size:5.5px">Tavenhurst Bowling Club</div>

<footer class="abs footer"></footer>
<h3 class="abs heading footer-heading" style="left:92px">Site Map</h3>
<div class="abs footer-heading-rule"></div>
<ul class="abs sitemap">
  <li>Become A Referee</li><li>News</li><li>Fixture &amp; Results</li><li>Photo Gallery</li><li>Sponsor</li><li>Club</li><li>Contact Us</li>
</ul>

<h3 class="abs heading footer-heading" style="left:242px">Latest News</h3>
<svg class="abs" style="left:370px;top:1032px" width="22" height="9" viewBox="0 0 22 9" aria-hidden="true">
  <circle cx="4.5" cy="4.5" r="4.5" fill="#555"/><path d="M5.5 2.5 3.5 4.5l2 2" fill="none" stroke="#ccc" stroke-width="1"/>
  <circle cx="16.5" cy="4.5" r="4.5" fill="#d4171f"/><path d="M15.5 2.5l2 2-2 2" fill="none" stroke="#fff" stroke-width="1"/>
</svg>
<div class="abs news-item" style="top:1062px">
  <div class="news-thumb" role="img" aria-label="Match photo"></div>
  <p class="news-text">Lorem Ipsum is simply dummy text<br>of the typesetting industry.</p>
  <p class="news-date">Mar 11, 2014</p>
</div>
<div class="abs news-item" style="top:1096px">
  <div class="news-thumb" role="img" aria-label="Match photo"></div>
  <p class="news-text">Lorem Ipsum is simply dummy text<br>of the typesetting industry.</p>
  <p class="news-date">Mar 11, 2014</p>
</div>
<div class="abs news-item" style="top:1129px">
  <div class="news-thumb" role="img" aria-label="Match photo"></div>
  <p class="news-text">Lorem Ipsum is simply dummy text<br>of the typesetting industry.</p>
  <p class="news-date">Mar 11, 2014</p>
</div>

<h3 class="abs heading footer-heading" style="left:444px">Photo Gallery</h3>
<span class="abs view-all">View All</span>
<div class="abs gallery" role="img" aria-label="Grid of club photos showing players and team groups">
  <div class="red"></div><div></div><div></div>
  <div class="red"></div><div class="red"></div><div class="green"></div>
  <div></div><div class="red"></div><div class="green"></div>
</div>

<div class="abs footer-rule"></div>
<p class="abs copyright">Copyright .TAVENHURST FC ® 2014. All rights reserved. Terms and Conditions</p>
<div class="abs social first" style="left:508px"></div>
<div class="abs social" style="left:526px"></div>
<div class="abs social" style="left:544px"></div>
<div class="abs social" style="left:562px"></div>
<div class="abs social" style="left:580px"></div>

</body>
</html>
```